Distribution/Printing company needs a web site to inform prospective customers on what we do.

Distribution/Printing/Packaging company needs a web site to inform prospective customers on what we do. Please look at our direct to consumer web site (under development) for an idea of the product lines we sell: storedev.maplewickhaven.com
Logo files are attached as is a flyer that is under development which contains other information about the company (this is to be used for content- not to be posted as is). The web site should be focused on our business customer base and is not intended to be direct to consumer. Site should have a link to our consumer web site.
Site design should be mobile friendly, or mobile could be redirected to a mobile version. This web site will be strictly informational and will not be designed for any sales transactions.

Target Market(s)

Manufacturing and retail businesses, any other multi-site business that would benefit from centralized pricing and budget controls we can provide (banks, medical/dental offices, educational facilities, etc).

Industry/Entity Type

It Company

Coding

Coded - Design and coding required

Number of Pages Required

5+ page

Requirements
Must have
• 1) Top level menu: Products, about us, locations, contact us, news
• 2) page with news/promotions that is easily updated
• 3) "contact us" form (name, company, phone, email address) email link
• 4) link to www.store.maplewickhaven.com with information that lower pricing is available for businesses
• 5) SEO keywords
• 6) Link to powerpoint presentation file
Nice to have
• 1) our phone number should appear on every page near the top

```html
<!DOCTYPE html>
<html lang="en">
<head>
<meta charset="utf-8">
<title>Maplewick Haven Supply — Packaging, Printing, Distribution</title>
<link rel="stylesheet" href="https://fonts.googleapis.com/css2?family=Maven+Pro:wght@500;700&family=Arimo:wght@400;700&display=swap">
<style>
  :root {
    --blue-deep: #0a3f69;
    --blue-mid: #1a6fa6;
    --blue-text: #1b6aa3;
    --beige: #e6dfd2;
    --beige-dark: #cfc6b6;
    --canvas: #efede8;
    --white: #ffffff;
    --ink: #555555;
    --field-border: #cfcfcf;
    --warn: #e0a020;
    --maroon: #8e2b3a;
  }
  * { box-sizing: border-box; margin: 0; padding: 0; }
  html, body { width: 1196px; height: 1200px; overflow: hidden; }
  body {
    position: relative;
    background: var(--canvas);
    font-family: "Arimo", Arial, sans-serif;
    color: var(--ink);
  }

  /* Header */
  .site-header {
    position: absolute; left: 0; top: 0; width: 1196px; height: 86px;
    background: linear-gradient(to bottom, #1d6ea3 0%, #10507f 55%, var(--blue-deep) 100%);
  }
  .brand-mark { position: absolute; left: 238px; top: 12px; width: 14px; height: 14px; background: var(--white); }
  .brand {
    position: absolute; left: 197px; top: 50px; width: 166px; text-align: center;
    color: var(--white); font-family: "Maven Pro", sans-serif; font-weight: 700;
    font-size: 12.5px; line-height: 14px; white-space: nowrap;
  }
  .brand-tag {
    position: absolute; left: 197px; top: 67px; width: 166px; text-align: center;
    color: var(--white); font-size: 9.5px; font-weight: 700; white-space: nowrap;
  }
  .lang-select {
    position: absolute; left: 840px; top: 33px; width: 128px; height: 23px;
    background: var(--white); border-radius: 3px; border: 1px solid #b9c6d2;
    font-size: 11px; font-weight: 700; color: #333; padding: 4px 7px;
  }
  .lang-select::after {
    content: ""; position: absolute; right: 8px; top: 8px;
    border: 3px solid transparent; border-top-color: #333;
  }
  .flag { position: absolute; left: 975px; top: 34px; }

  /* Navigation */
  .main-nav {
    position: absolute; left: 0; top: 86px; width: 1196px; height: 40px;
    background: linear-gradient(to bottom, #efe9de, var(--beige));
    border-top: 1px solid #f6f2ea; border-bottom: 1px solid var(--beige-dark);
    display: flex; padding-left: 197px;
  }
  .main-nav a {
    display: block; height: 38px; line-height: 38px; text-align: center;
    font-size: 13.5px; color: #1b4e78; text-decoration: none;
    border-right: 1px solid var(--beige-dark);
  }

  /* Hero */
  .hero-band { position: absolute; left: 0; top: 126px; width: 1196px; height: 259px; background: var(--white); }
  .hero {
    position: absolute; left: 189px; top: 126px; width: 818px; height: 248px;
    background: radial-gradient(ellipse at 60% 45%, #ded6c6 0%, #cfc8bb 45%, #bdb6aa 100%);
  }
  .hero-product {
    position: absolute; left: 253px; top: 0; width: 310px; height: 232px;
    background: linear-gradient(160deg, #b27b4a 0%, #8e5b33 55%, #2d3348 56%, #1f2536 100%);
  }
  .hero-name {
    position: absolute; left: 229px; top: 233px; width: 186px; text-align: center;
    color: var(--maroon); font-family: "Maven Pro", sans-serif; font-weight: 700;
    font-size: 13px; line-height: 16px; white-space: nowrap;
  }
  .hero-tag {
    position: absolute; left: 229px; top: 252px; width: 186px; text-align: center;
    color: var(--maroon); font-family: "Maven Pro", sans-serif; font-weight: 700;
    font-size: 10.5px; white-space: nowrap;
  }
  .hero-arrow { position: absolute; top: 230px; }
  .hero-dots { position: absolute; left: 900px; top: 362px; display: flex; gap: 3px; }
  .hero-dots span { width: 7px; height: 7px; border-radius: 50%; background: #c59a9a; }
  .hero-dots span:first-child { background: var(--maroon); }

  /* Services */
  .service-photo {
    position: absolute; width: 172px; height: 172px; border-radius: 50%;
    border: 4px solid var(--white); box-shadow: 0 0 0 1px #d8d4cc, 0 3px 6px rgba(0,0,0,.12);
  }
  .service-shadow {
    position: absolute; width: 90px; height: 8px; border-radius: 50%;
    background: radial-gradient(ellipse, rgba(0,0,0,.22), rgba(0,0,0,0) 70%);
  }
  .service-title {
    position: absolute; width: 200px; text-align: center;
    font-family: "Maven Pro", sans-serif; font-weight: 700; font-size: 21px; color: var(--blue-text);
  }
  .service-curve { position: absolute; }
  .service-card {
    position: absolute; width: 202px; height: 142px; background: var(--white);
    box-shadow: 0 1px 3px rgba(0,0,0,.15); padding: 35px 7px 0 13px;
    font-size: 11px; line-height: 13.4px; color: #666;
  }
  .service-card .read-more {
    display: block; text-align: center; margin-top: 5px; color: #1b5f97; text-decoration: none;
  }

  /* Forms */
  .section-title {
    position: absolute; font-family: "Maven Pro", sans-serif; font-weight: 500;
    font-size: 18.5px; color: var(--blue-text);
  }
  .field {
    position: absolute; background: var(--white); border: 1px solid var(--field-border);
    border-radius: 5px; font-size: 11px; color: #888; padding: 5px 8px;
  }
  .btn {
    position: absolute; background: linear-gradient(to bottom, #2a7fb6, #115a8e);
    border-radius: 5px; color: var(--white); font-weight: 700; font-size: 12.5px;
    text-align: center; border: 1px solid #0c4a78;
  }
  .status {
    position: absolute; left: 331px; top: 948px; font-size: 11px; color: var(--warn);
    display: flex; align-items: center; gap: 5px;
  }
  .pay-options { position: absolute; left: 754px; top: 939px; width: 254px; display: flex; justify-content: space-between; align-items: center; }
  .pay-badge {
    height: 30px; padding: 0 7px; line-height: 30px; border-radius: 4px;
    background: #e2e0db; color: #8f8f8f; font-weight: 700; font-size: 12px; white-space: nowrap;
  }

  /* Footer */
  .site-footer {
    position: absolute; left: 0; top: 999px; width: 1196px; height: 201px;
    background: linear-gradient(to bottom, var(--blue-mid) 0%, #15609a 45%, var(--blue-deep) 100%);
    color: var(--white);
  }
  .footer-col { position: absolute; top: 22px; font-size: 10.8px; line-height: 14px; }
  .footer-col h3 {
    font-family: "Maven Pro", sans-serif; font-weight: 500; font-size: 17px; margin-bottom: 11px;
  }
  .partner-list { list-style: none; width: 160px; }
  .partner-list li { height: 25.5px; border-bottom: 1px solid rgba(255,255,255,.12); padding-top: 1px; }
  .partner-list li:last-child { border-bottom: none; }
  .footer-col p + p { margin-top: 15px; }
  .social { display: flex; gap: 14px; margin-top: 20px; }
  .social span { display: flex; align-items: center; gap: 5px; color: #93a9bd; font-weight: 700; font-size: 11px; }
  .social i { width: 14px; height: 14px; border-radius: 50%; background: #6f8396; }
  .copyright { position: absolute; left: 0; top: 182px; width: 1196px; text-align: center; font-size: 11px; }
</style>
</head>
<body>

<header class="site-header">
  <span class="brand-mark"></span>
  <div class="brand">MAPLEWICK HAVEN SUPPLY</div>
  <div class="brand-tag">Packaging • Printing • Distribution</div>
  <div class="lang-select">Select Language</div>
  <svg class="flag" width="33" height="22" viewBox="0 0 33 22" aria-hidden="true">
    <rect width="33" height="22" fill="#ffffff"/>
    <g fill="#c0283a">
      <rect y="0" width="33" height="2"/><rect y="4" width="33" height="2"/><rect y="8" width="33" height="2"/>
      <rect y="12" width="33" height="2"/><rect y="16" width="33" height="2"/><rect y="20" width="33" height="2"/>
    </g>
    <rect width="14" height="12" fill="#2b3f7e"/>
  </svg>
</header>

<nav class="main-nav">
  <a href="#" style="width:89px">Packaging</a>
  <a href="#" style="width:110px">Office Supplies</a>
  <a href="#" style="width:77px">Janitorial</a>
  <a href="#" style="width:112px">Retail Supplies</a>
  <a href="#" style="width:82px">About Us</a>
  <a href="#" style="width:90px;border-right:none">Contact US</a>
</nav>

<div class="hero-band"></div>
<div class="hero" role="img" aria-label="Photo of a printed kraft gift box holding patterned ornaments">
  <div class="hero-product"></div>
</div>
<div class="hero-name">MAPLEWICK HAVEN SUPPLY</div>
<div class="hero-tag">Packaging • Printing • Distribution</div>
<svg class="hero-arrow" style="left:206px" width="14" height="18" viewBox="0 0 14 18" aria-hidden="true"><path d="M12 1 L3 9 L12 17" fill="none" stroke="#8e2b3a" stroke-width="4"/></svg>
<svg class="hero-arrow" style="left:976px" width="14" height="18" viewBox="0 0 14 18" aria-hidden="true"><path d="M2 1 L11 9 L2 17" fill="none" stroke="#8e2b3a" stroke-width="4"/></svg>
<div class="hero-dots"><span></span><span></span><span></span></div>

<div class="service-photo" role="img" aria-label="Photo of kraft product boxes with green leaf print" style="left:226px;top:410px;background:radial-gradient(circle at 45% 55%,#8f9a55,#a8916a 55%,#6d5e47)"></div>
<div class="service-photo" role="img" aria-label="Photo of green printed folding cartons and bags" style="left:512px;top:410px;background:radial-gradient(circle at 50% 55%,#5e9c3a,#3f7d2a 55%,#c9b48f)"></div>
<div class="service-photo" role="img" aria-label="Photo of a wooden crate filled with honey jars" style="left:807px;top:410px;background:radial-gradient(circle at 50% 50%,#a8794a,#c9ab82 60%,#8b6b4a)"></div>

<div class="service-shadow" style="left:267px;top:594px"></div>
<div class="service-shadow" style="left:553px;top:594px"></div>
<div class="service-shadow" style="left:848px;top:594px"></div>

<h2 class="service-title" style="left:212px;top:604px">Packaging</h2>
<h2 class="service-title" style="left:498px;top:604px">Printing</h2>
<h2 class="service-title" style="left:793px;top:606px">Distribution</h2>

<svg class="service-curve" style="left:176px;top:640px" width="260" height="170" viewBox="0 0 260 170" aria-hidden="true"><path d="M50 12 C5 40 0 130 70 160 C130 175 190 160 230 150" fill="none" stroke="#dedad2" stroke-width="10"/></svg>
<svg class="service-curve" style="left:470px;top:640px" width="260" height="170" viewBox="0 0 260 170" aria-hidden="true"><path d="M50 12 C5 40 0 130 70 160 C130 175 190 160 230 150" fill="none" stroke="#dedad2" stroke-width="10"/></svg>
<svg class="service-curve" style="left:763px;top:640px" width="260" height="170" viewBox="0 0 260 170" aria-hidden="true"><path d="M50 12 C5 40 0 130 70 160 C130 175 190 160 230 150" fill="none" stroke="#dedad2" stroke-width="10"/></svg>

<article class="service-card" style="left:202px;top:651px">Lorem ipsum dolor sit amet, consecte-tur adipisicing elit, sed do eiusmod tempor incididunt ut labore et dolore magna aliqua. Ut enim ad minim veniam, quis nostrud exercitation<a class="read-more" href="#">Read More</a></article>
<article class="service-card" style="left:496px;top:651px">Lorem ipsum dolor sit amet, consecte-tur adipisicing elit, sed do eiusmod tempor incididunt ut labore et dolore magna aliqua. Ut enim ad minim veniam, quis nostrud exercitation<a class="read-more" href="#">Read More</a></article>
<article class="service-card" style="left:789px;top:651px">Lorem ipsum dolor sit amet, consecte-tur adipisicing elit, sed do eiusmod tempor incididunt ut labore et dolore magna aliqua. Ut enim ad minim veniam, quis nostrud exercitation<a class="read-more" href="#">Read More</a></article>

<h2 class="section-title" style="left:189px;top:840px">Send us a Message</h2>
<div class="field" style="left:190px;top:873px;width:128px;height:23px">Your mail</div>
<div class="field" style="left:190px;top:906px;width:128px;height:23px">Your name</div>
<div class="field" style="left:330px;top:873px;width:296px;height:56px">Your message</div>
<div class="status">
  <svg width="14" height="12" viewBox="0 0 14 12" aria-hidden="true"><path d="M7 0 L14 12 H0 Z" fill="#e8a020"/><rect x="6.2" y="4" width="1.6" height="4.5" fill="#fff"/><rect x="6.2" y="9.3" width="1.6" height="1.6" fill="#fff"/></svg>
  Your message has been sent!
</div>
<div class="btn" style="left:538px;top:941px;width:88px;height:27px;line-height:25px">Send</div>

<h2 class="section-title" style="left:700px;top:841px">Newsletter</h2>
<div class="field" style="left:700px;top:874px;width:210px;height:27px;padding-top:7px">Your@awesome-email.com</div>
<div class="btn" style="left:920px;top:874px;width:87px;height:27px;line-height:25px">Subscribe!</div>
<div class="pay-options">
  <span class="pay-badge">Paywise</span>
  <span class="pay-badge">Meridian Card</span>
  <span class="pay-badge">Vantage</span>
</div>

<footer class="site-footer">
  <div class="footer-col" style="left:209px">
    <h3>Partners</h3>
    <ul class="partner-list">
      <li>partnerexample.com</li><li>partnerexample.com</li><li>partnerexample.com</li><li>partnerexample.com</li><li>partnerexample.com</li>
    </ul>
  </div>
  <div class="footer-col" style="left:404px;width:200px">
    <h3>Blogs</h3>
    <p style="width:200px;letter-spacing:-.15px">We make fresh, creative and professional web design for our clients.</p>
    <p style="width:200px;letter-spacing:-.15px">If you want us to design your dream website contact us</p>
  </div>
  <div class="footer-col" style="left:639px;width:175px">
    <h3>Get Social</h3>
    <p>Follow us on below applications and be upadated.</p>
    <div class="social"><span><i></i>Chirp</span><span><i></i>Facet</span><span><i></i>Linkly</span></div>
  </div>
  <div class="footer-col" style="left:836px;width:190px">
    <h3>Contact Details</h3>
    <p>Contact details will be appear here contact details here</p>
    <p>Phone No. : 00 123 480-7716</p>
    <p>E-mail : info@maplewickhaven.com</p>
  </div>
  <div class="copyright">All Right Reserved 2015. Maplewick Haven Supply.</div>
</footer>

</body>
</html>
```